Personal development products that change your life

This is a direct selling business that sells personal development courses, but also sells the business as well if desired. This is not MLM, and there is no handling of the product required, nor hassling friends or family. We are looking for business minded people wanting to work their own hours and achieve a desirable income from this. A success image or happy image on a flyer would be great. I'd like the website address to be displayed as well thanks. www.grow-and-gain.com.au

Target Market(s)

Business-minded individuals searching for more finances. Self motivated, driven, interested in self development.

Industry/Entity Type

Business

Font styles to use
Sans Serif

Requirements
Must have
• Are you looking for
• - a franchise or business?
• - a change of career?
• - a back up income?
• Not MLM
• No product handling or shipping
• No hard sales required
• website: www.grow-and-gain.com.au
Nice to have
• A picture or background of excited person jumping in the air, or some similar.
• Worded to enrol people interested in achieving more financial headway, or flexible hours, or travel and do this business from anywhere in the world.
• Only need access to a phone, internet connection and a desire to succeed.

```html
<!DOCTYPE html>
<html lang="en">
<head>
<meta charset="utf-8">
<title>Grow and Gain flyer</title>
<link href="https://fonts.googleapis.com/css2?family=Oswald:wght@700&family=Arimo:wght@400&display=swap" rel="stylesheet">
<style>
  :root {
    --blue: #2d7ff0;
    --blue-deep: #1f6fe0;
    --ink: #111111;
    --white: #ffffff;
    --rule: #9a9a9a;
    --mist: #dcebfb;
    --sun-hot: #ffb23a;
    --sun-mid: #f07a12;
    --sun-dark: #6a2a05;
  }
  * { margin: 0; padding: 0; box-sizing: border-box; }
  html, body { width: 847px; height: 1200px; overflow: hidden; background: var(--white); }
  .flyer {
    position: relative;
    width: 847px;
    height: 1200px;
    overflow: hidden;
    font-family: "Arimo", Arial, sans-serif;
    color: var(--ink);
    background: var(--white);
  }
  .title {
    position: absolute;
    top: 8px; left: 0; width: 100%;
    text-align: center;
    font-family: "Oswald", "Arial Narrow", sans-serif;
    font-weight: 700;
    font-size: 100px;
    line-height: 112px;
    letter-spacing: 2px;
    white-space: nowrap;
  }
  .tagline {
    position: absolute;
    top: 127px; left: 0; width: 100%; height: 85px;
    background: var(--blue);
    color: var(--white);
    font-size: 46px;
    line-height: 85px;
    text-align: center;
  }
  .hero {
    position: absolute;
    top: 212px; left: 0; width: 100%; height: 368px;
    background: radial-gradient(ellipse at 62% 55%, var(--sun-hot) 0%, var(--sun-mid) 40%, var(--sun-dark) 100%);
  }
  .rail {
    position: absolute;
    width: 4px;
    background: var(--white);
  }
  .pill {
    position: absolute;
    left: 85px;
    height: 48px;
    padding: 0 26px 0 18px;
    background: var(--blue);
    color: var(--white);
    font-size: 30px;
    line-height: 48px;
    border-radius: 0 24px 24px 0;
    white-space: nowrap;
  }
  .hero .pill { font-size: 26px; padding-right: 22px; }
  .pill::before {
    content: "";
    position: absolute;
    left: -45px; top: 22px;
    width: 45px; height: 4px;
    background: var(--white);
  }
  .pill--benefit::before { background: var(--blue); opacity: .55; }
  .question {
    position: absolute;
    top: 588px; left: 0; width: 100%;
    text-align: center;
    font-size: 28px;
    line-height: 40px;
  }
  .needs {
    position: absolute;
    top: 642px; left: 0; width: 100%; height: 46px;
    border-top: 2px solid var(--rule);
    border-bottom: 2px solid var(--rule);
    text-align: center;
    font-size: 23px;
    line-height: 42px;
  }
  .benefits {
    position: absolute;
    top: 688px; left: 0; width: 100%; height: 392px;
    background: linear-gradient(180deg, var(--white) 0%, var(--mist) 100%);
  }
  .benefits .rail { background: var(--blue); opacity: .55; }
  .footer {
    position: absolute;
    top: 1080px; left: 0; width: 100%; height: 120px;
    background: var(--blue);
    color: var(--white);
    text-align: center;
  }
  .footer__cta {
    position: absolute; top: 12px; left: 0; width: 100%;
    font-size: 32px; line-height: 44px;
  }
  .footer__rule {
    position: absolute; top: 64px; left: 0; width: 100%; height: 2px;
    background: var(--blue-deep);
  }
  .footer__web {
    position: absolute; top: 74px; left: 0; width: 100%;
    font-size: 26px; line-height: 40px;
  }
</style>
</head>
<body>
<main class="flyer">
  <h1 class="title">GROW AND GAIN</h1>
  <p class="tagline">Start the life you always wanted</p>

  <section class="hero" role="img" aria-label="Silhouette of a person with arms raised in celebration against an orange sunset sky">
    <div class="rail" style="left:40px; top:85px; height:190px;"></div>
    <div class="pill" style="top:61px;">Are you looking for</div>
    <div class="pill" style="top:126px;">A franchise or business?</div>
    <div class="pill" style="top:189px;">A change of career?</div>
    <div class="pill" style="top:251px;">A back up income?</div>
  </section>

  <p class="question">What makes you able for this?</p>
  <p class="needs">You need access to a phone, internet connection and a desire to succeed.</p>

  <section class="benefits">
    <div class="rail" style="left:40px; top:110px; height:186px;"></div>
    <div class="pill pill--benefit" style="top:86px;">Your Benifits</div>
    <div class="pill pill--benefit" style="top:143px;">Not MLM</div>
    <div class="pill pill--benefit" style="top:205px;">No hard sales required</div>
    <div class="pill pill--benefit" style="top:270px;">No product handling and shipping</div>
  </section>

  <footer class="footer">
    <p class="footer__cta">Vist today</p>
    <div class="footer__rule"></div>
    <p class="footer__web">website: www.grow-and-gain.com.au</p>
  </footer>
</main>
</body>
</html>
```